first fantastic look and impression

We are looking for a concept for letterhead, business card, emailfooter and template for invoices or offers for our company in the consultation business.
The dancer is a symbol who we are: it looks simple, but there is a lot of hard work and many years of training in this movement. The look is also what we want: elegant, modern, strong, with a touch of extravaganza
Target Market(s)
Hotelbusiness , Consulting
Font styles to use
Sans Serif
Other font styles liked:
- please give us a option we are open
Requirements
Must have
- We are not typical consultants but sparring partners and coaches for the hotel and that should also be expressed in the design. Maybe there is an icon that supports the whole thing. We are more modern and bolder than our industry colleagues.
we are modern, fresh, agile, fast
Nice to have
- a icon

```html
<!DOCTYPE html>
<html lang="en">
<head>
<meta charset="utf-8">
<title>Corvane Hotel Coaching Letterhead</title>
<link href="https://fonts.googleapis.com/css2?family=EB+Garamond:wght@400;500&family=Open+Sans:wght@400;600;700&display=swap" rel="stylesheet">
<style>
  :root {
    --backdrop: #dadddf;
    --paper: #ffffff;
    --brand-blue: #4f6f94;
    --brand-gold: #d9c08e;
    --headline-grey: #cfd2d6;
    --text-dark: #3d4e63;
    --text-muted: #6b7684;
  }
  html, body {
    margin: 0;
    width: 1200px;
    height: 784px;
    overflow: hidden;
    background: var(--backdrop);
  }
  .canvas {
    position: relative;
    width: 1200px;
    height: 784px;
    display: flex;
    align-items: center;
    justify-content: center;
  }
  .letterhead {
    position: relative;
    width: 523px;
    height: 740px;
    background: var(--paper);
    box-shadow: 0 6px 22px rgba(60, 70, 80, 0.18);
    overflow: hidden;
  }
  .top-accent {
    position: absolute;
    left: 14px;
    top: 14px;
    width: 48px;
    height: 5px;
    background: var(--brand-gold);
  }
  .logo-photo {
    position: absolute;
    left: 44px;
    top: 26px;
    width: 66px;
    height: 42px;
    border-radius: 40% 50% 45% 40%;
    background: linear-gradient(135deg, #2e4766 0%, #5a7598 55%, #c9a488 100%);
  }
  .brand-name {
    position: absolute;
    left: 74px;
    top: 80px;
    margin: 0;
    font-family: "Open Sans", sans-serif;
    font-weight: 400;
    font-size: 13px;
    letter-spacing: 0.4px;
    color: var(--brand-blue);
    white-space: nowrap;
  }
  .header-band {
    position: absolute;
    left: 222px;
    top: 104px;
    right: 0;
    height: 7px;
    background: var(--brand-blue);
  }
  .headline {
    position: absolute;
    left: 58px;
    top: 610px;
    margin: 0;
    transform-origin: 0 0;
    transform: rotate(-90deg);
    white-space: nowrap;
    font-family: "EB Garamond", serif;
    font-weight: 400;
    font-size: 25px;
    letter-spacing: 0.6px;
    color: var(--headline-grey);
  }
  .watermark-figure {
    position: absolute;
    left: 120px;
    top: 200px;
    width: 300px;
    height: 330px;
    border-radius: 45% 55% 50% 50%;
    background: radial-gradient(ellipse at 45% 45%, #e4e6e9 0%, #eef0f2 55%, rgba(255,255,255,0) 75%);
  }
  .contact {
    position: absolute;
    left: 20px;
    top: 640px;
    margin: 0;
    padding: 0;
    list-style: none;
    font-family: "Open Sans", sans-serif;
    font-size: 9.5px;
    line-height: 15px;
  }
  .contact li {
    display: flex;
    align-items: center;
    gap: 5px;
    white-space: nowrap;
  }
  .contact .address { font-weight: 700; color: var(--text-dark); }
  .contact .email { font-weight: 400; color: var(--text-muted); }
  .contact svg { width: 10px; height: 10px; flex: none; }
  .footer-bands {
    position: absolute;
    left: 0;
    bottom: 0;
    width: 523px;
    height: 50px;
  }
  .web-address {
    position: absolute;
    right: 18px;
    bottom: 9px;
    margin: 0;
    font-family: "Open Sans", sans-serif;
    font-weight: 600;
    font-size: 14px;
    color: #ffffff;
    letter-spacing: 0.2px;
    white-space: nowrap;
  }
</style>
</head>
<body>
<main class="canvas">
  <article class="letterhead">
    <div class="top-accent"></div>
    <div class="logo-photo" role="img" aria-label="Small photo of a dancer in a flowing blue dress"></div>
    <p class="brand-name">Corvane Hotel Coaching</p>
    <div class="header-band"></div>

    <div class="watermark-figure" role="img" aria-label="Faint large photo of a dancer with flowing fabric"></div>
    <h1 class="headline">We are sparring partners for successful hotels</h1>

    <ul class="contact">
      <li class="address">
        <svg viewBox="0 0 10 10" aria-hidden="true"><circle cx="5" cy="5" r="5" fill="var(--brand-blue)"/><path d="M5 2.2a1.8 1.8 0 0 0-1.8 1.8c0 1.4 1.8 3.6 1.8 3.6s1.8-2.2 1.8-3.6A1.8 1.8 0 0 0 5 2.2z" fill="#fff"/></svg>
        Corvane Hotel Coaching, Bregenz/Austria
      </li>
      <li class="email">
        <svg viewBox="0 0 10 10" aria-hidden="true"><circle cx="5" cy="5" r="5" fill="var(--brand-blue)"/><rect x="2.5" y="3.3" width="5" height="3.4" fill="none" stroke="#fff" stroke-width="0.7"/><path d="M2.5 3.3 5 5.3 7.5 3.3" fill="none" stroke="#fff" stroke-width="0.7"/></svg>
        info@corvane-coaching.com
      </li>
    </ul>

    <svg class="footer-bands" viewBox="0 0 523 50" aria-hidden="true">
      <rect x="14" y="15" width="110" height="4" fill="var(--brand-gold)"/>
      <rect x="132" y="15" width="72" height="4" fill="var(--brand-blue)"/>
      <rect x="212" y="15" width="120" height="4" fill="var(--brand-gold)"/>
      <rect x="0" y="26" width="336" height="9" fill="var(--brand-blue)"/>
      <polygon points="344,8 523,8 523,50 330,50" fill="var(--brand-blue)"/>
    </svg>
    <p class="web-address">corvane-coaching.com</p>
  </article>
</main>
</body>
</html>
```